Business Card Design Project

We need a business card for a new technology services company. We develop software and implement software packages for our business customers and although we will begin with just one or two service offerings, our service offerings will expand over time. Our name comes from the an author, KL Barrow, and his "idea" was that opportunity should be based on ability and achievement, not on social status.

We would like to see a design that is standard in its size and shape, but stands apart in its dramatic color contrasts. The card should not use too many colors - the colors used in the background should highlight the brilliant blues of the logo (see attachment) to dramatic effect. The background should not be white.

If necessary, you can change the color of the words "KL Barrow", but not the word "Idea".

Card size should be U.S. standard 2 inches by 3.5 inches and provide for 1/8 inch bleed area on each side.

We need a design for both sides of the business card, one side communicating the company logo and contact information, the other side being purely graphical, incorporating the logo but no other information.

Contact Information Required:
Kate Brook
KateBrook@klbarrowvista.com
614-387-2259

Target Market(s)

Business executives

Industry/Entity Type

Software

Requirements
Must have
• It must have the full company logo on one side, and at least the graphic element of the logo on the other. Either that or the full logo on both.
Nice to have
• It would be nice to have a design that could work without needing two different textures. For example, it would be nice if the entire card could be shiny, not just parts of the card.

It would also be nice if texture is something we could add later.
Should not have
• The card should not use the color green.

```html
<!DOCTYPE html>
<html lang="en">
<head>
<meta charset="utf-8">
<title>KL Barrow Vista – Business Card</title>
<link href="https://fonts.googleapis.com/css2?family=Roboto:wght@300;400;700&display=swap" rel="stylesheet">
<style>
  :root {
    --page: #e6e2dc;
    --card-dark: #141414;
    --card-mid: #2b2b2b;
    --card-light: #3a3a3a;
    --brand-blue: #1aa3e0;
    --text-light: #d8d8d8;
    --text-soft: #b9b9b9;
    --tab-grey: #9a9a9a;
  }
  * { margin: 0; padding: 0; box-sizing: border-box; }
  html, body {
    width: 1200px;
    height: 720px;
    overflow: hidden;
    background: var(--page);
    font-family: "Roboto", Arial, sans-serif;
  }
  .sheet {
    width: 1200px;
    height: 720px;
    display: flex;
    align-items: center;
    justify-content: center;
    gap: 60px;
  }
  .card {
    position: relative;
    width: 520px;
    height: 297px;
    overflow: hidden;
    background:
      radial-gradient(ellipse at 55% 35%, var(--card-light) 0%, var(--card-mid) 35%, var(--card-dark) 80%);
    box-shadow: 0 6px 18px rgba(0,0,0,0.25);
  }

  /* Contact side */
  .wordmark {
    position: absolute;
    display: flex;
    align-items: center;
    gap: 10px;
    color: var(--text-light);
    font-weight: 300;
    letter-spacing: -0.5px;
    white-space: nowrap;
  }
  .wordmark-dot {
    border-radius: 50%;
    background: var(--brand-blue);
    flex: none;
  }
  .card-front .wordmark { left: 38px; top: 132px; font-size: 36px; }
  .card-front .wordmark-dot { width: 16px; height: 16px; }

  .holder-name {
    position: absolute;
    right: 34px;
    top: 160px;
    color: var(--brand-blue);
    font-weight: 700;
    font-size: 18px;
    letter-spacing: 0.5px;
    text-transform: uppercase;
  }
  .contact-list {
    position: absolute;
    left: 38px;
    top: 222px;
    list-style: none;
    color: var(--text-soft);
    font-size: 13px;
    font-weight: 400;
  }
  .contact-item {
    display: flex;
    align-items: center;
    gap: 8px;
    height: 22px;
  }
  .contact-icon { width: 11px; height: 11px; flex: none; }

  .edge-tab {
    position: absolute;
    width: 7px;
  }
  .edge-tab-blue {
    left: 0;
    top: 226px;
    height: 44px;
    background: var(--brand-blue);
    border-radius: 0 4px 4px 0;
  }
  .edge-tab-grey {
    right: 0;
    top: 52px;
    height: 30px;
    background: var(--tab-grey);
    border-radius: 4px 0 0 4px;
  }

  /* Graphic side */
  .card-back .wordmark { left: 34px; top: 210px; font-size: 50px; }
  .card-back .wordmark-dot { width: 22px; height: 22px; }
  .brand-disc {
    position: absolute;
    right: 70px;
    top: 36px;
    width: 150px;
    height: 150px;
    border-radius: 50%;
    background: var(--brand-blue);
  }
</style>
</head>
<body>
  <main class="sheet">
    <section class="card card-front" aria-label="Business card, contact side">
      <div class="wordmark">
        <span class="wordmark-text">KL Barrow Vista</span>
        <span class="wordmark-dot"></span>
      </div>
      <p class="holder-name">Kate Brook</p>
      <ul class="contact-list">
        <li class="contact-item">
          <svg class="contact-icon" viewBox="0 0 12 12" aria-hidden="true">
            <circle cx="6" cy="6" r="5.2" fill="none" stroke="#b9b9b9" stroke-width="1.2"/>
            <path d="M4.2 3.4 L5.2 4.6 L4.7 5.3 Q5.4 6.7 6.7 7.3 L7.4 6.8 L8.6 7.8 L7.9 8.7 Q5 8.6 3.3 4.2 Z" fill="#b9b9b9"/>
          </svg>
          <span>614-387-2259</span>
        </li>
        <li class="contact-item">
          <svg class="contact-icon" viewBox="0 0 12 12" aria-hidden="true">
            <rect x="1" y="2.5" width="10" height="7" rx="1" fill="none" stroke="#1aa3e0" stroke-width="1.2"/>
            <path d="M1.5 3 L6 6.5 L10.5 3" fill="none" stroke="#1aa3e0" stroke-width="1.2"/>
          </svg>
          <span>KateBrook@klbarrowvista.com</span>
        </li>
      </ul>
      <span class="edge-tab edge-tab-blue"></span>
      <span class="edge-tab edge-tab-grey"></span>
    </section>

    <section class="card card-back" aria-label="Business card, graphic side">
      <div class="brand-disc" role="img" aria-label="Area for the company's blue graphic emblem"></div>
      <div class="wordmark">
        <span class="wordmark-text">KL Barrow Vista</span>
      </div>
    </section>
  </main>
</body>
</html>
```